Navoro & Omvar Automotive Repair Shop. Need a new website design.

We specialize in Navoro & Omvar auto repair, but also work on other Asian import vehicles. We have been in business for 7 years and pride ourselves on high quality auto repair that is fixed right the first time. Would like the automotive repair website to incorporate the colors black, red and white if possible and have our logo and some Navoro and Omvar vehicles included in the website.

Target Market(s)

Navoro & Omvar vehicle owners

Industry/Entity Type

Automotive Repair

Coding

Coded - Design and coding required

Number of Pages Required

5+ page

Colors
EB3D1F
EC4F4E
F09395
F8D3D4
FCEDEE

Requirements
Must have
• Home, Services, Contact Us, Schedule appointment, and a gallery tab that I can add shop pictures to when completed.
Nice to have
• Would like to see example pictures of job next to each service listed.
Should not have
• Service not related to auto repair. Ex. auto detailing, towing, car wash

```html
<!DOCTYPE html>
<html lang="en">
<head>
<meta charset="utf-8">
<title>Kestrel Automotive – Navoro &amp; Omvar Auto Repair</title>
<link href="https://fonts.googleapis.com/css2?family=Krona+One&family=Roboto:wght@400;500;700&display=swap" rel="stylesheet">
<style>
:root{
  --red:#e3120b;
  --red-bright:#f0201a;
  --red-dark:#6e0404;
  --black:#000;
  --silver:#a9a9a9;
  --silver-dark:#6c6c6c;
  --white:#fff;
  --muted:#cfcfcf;
  --field:#111;
  --field-line:#3a3a3a;
  --heading:"Krona One",sans-serif;
  --body:"Roboto",sans-serif;
}
*{box-sizing:border-box;margin:0;padding:0}
html,body{width:1200px;height:4684px;overflow:hidden;background:var(--black)}
body{font-family:var(--body);color:var(--white)}
.page{position:relative;width:1200px;height:4684px;overflow:hidden;background:var(--black)}
.abs{position:absolute}
a{color:inherit;text-decoration:none}

/* top bar & nav */
.topbar{top:0;left:0;width:1200px;height:40px;background:var(--red);font-size:12px;font-weight:500}
.topbar span{position:absolute;top:12px;display:flex;align-items:center;gap:6px}
.nav{top:40px;left:0;width:1200px;height:78px;background:var(--black)}
.nav a{position:absolute;top:30px;font-size:13px;font-weight:500}
.btn{display:flex;align-items:center;justify-content:center;gap:8px;font-weight:700;font-size:13px;color:var(--white);background:var(--red);border:2px solid var(--white);border-radius:3px}
.nav .btn{top:16px;left:922px;width:136px;height:39px}
.logo-plate{top:0;left:518px;width:164px;height:218px;z-index:5}
.logo-name{position:absolute;left:0;width:164px;top:86px;text-align:center;font-family:var(--heading);font-size:17px;color:var(--white)}

/* hero */
.hero{top:118px;left:0;width:1200px;height:746px;overflow:hidden}
.hero-photo{position:absolute;inset:0;background:
  radial-gradient(ellipse 300px 170px at 850px 360px,#ee2a1c 0%,#b8160f 40%,rgba(120,20,15,.6) 65%,transparent 85%),
  radial-gradient(ellipse 260px 60px at 860px 520px,rgba(0,0,0,.7),transparent 80%),
  linear-gradient(180deg,#2a3440 0%,#3d4855 30%,#4a5461 52%,#23282e 72%,#14171a 100%)}
.hero h1{position:absolute;left:140px;top:150px;font-family:var(--heading);font-size:40px;line-height:55px;font-weight:400}
.hero h1 .red{color:var(--red-bright)}
.hero p{position:absolute;left:140px;top:272px;width:460px;font-size:13px;line-height:23px;font-weight:500}
.hero .btn{position:absolute;left:140px;top:375px;width:222px;height:52px;font-size:14px}
.dots{position:absolute;left:556px;top:648px;display:flex;gap:5px}
.dots i{width:12px;height:12px;border-radius:50%;border:1.5px solid #bbb}
.dots i.on{background:var(--red);border-color:var(--red)}

/* headings */
.title{font-family:var(--heading);font-size:32px;letter-spacing:1px;color:var(--silver);font-weight:400}
.title .w{color:var(--white)}
.title-rule{display:inline-block;width:72px;height:4px;background:var(--red);vertical-align:middle;margin-left:16px}
.center-title{position:absolute;left:0;width:1200px;text-align:center}
.center-title::after{content:"";display:block;width:74px;height:4px;background:var(--red);margin:18px auto 0}

/* about */
.about{top:864px;left:0;width:1200px;height:536px}
.about .frame-back{left:218px;top:98px;width:324px;height:316px;border:5px solid #3d3d3d;border-radius:8px}
.about .photo-a{left:131px;top:45px;width:378px;height:313px;border:9px solid var(--red);border-radius:10px;background:
  radial-gradient(ellipse 120px 90px at 120px 170px,#1c1e22 0%,transparent 80%),
  linear-gradient(90deg,#2f55a8 0 6%,#cfd3d9 6% 70%,#2f55a8 70% 76%,#9aa0a8 76%)}
.about .photo-b{left:269px;top:199px;width:289px;height:232px;border:8px solid var(--black);background:
  radial-gradient(ellipse 70px 90px at 90px 110px,#8a8d93 0%,transparent 80%),
  radial-gradient(ellipse 70px 110px at 220px 140px,#111 0%,transparent 85%),
  linear-gradient(180deg,#d9dde2,#7e838b 60%,#3a3c40)}
.about h2{position:absolute;left:649px;top:84px}
.about .copy{position:absolute;left:649px;top:146px;width:406px;font-size:12.5px;line-height:21.5px;color:var(--muted);text-align:justify}
.about .copy p+p{margin-top:14px}
.about .btn{position:absolute;left:649px;top:390px;width:142px;height:44px}

/* brands */
.brands{top:1400px;left:0;width:1200px;height:490px}
.brands h2{position:absolute;left:143px;top:80px}
.brands .lead{position:absolute;left:143px;top:138px;width:400px;font-size:12.5px;line-height:23px;color:var(--muted)}
.brand{position:absolute;display:flex;align-items:center;gap:12px;font-size:14px;font-weight:500}
.brand i{width:56px;height:56px;border-radius:50%;background:#2a2a2a;border:2px solid #3a3a3a}

/* services */
.services{top:1890px;left:0;width:1200px;height:477px;background:linear-gradient(90deg,var(--red) 0%,#c40c08 45%,var(--red-dark) 100%)}
.services .center-title{top:56px}
.services .center-title .dim{color:#5a5a5a}
.services .center-title::after{background:var(--white)}
.svc{position:absolute;display:flex;gap:10px;font-size:13px;font-weight:700;line-height:23px;width:215px}
.svc svg{flex:0 0 18px;margin-top:2px}
.services .btn{position:absolute;left:502px;top:370px;width:194px;height:44px;background:linear-gradient(90deg,#3a0202,var(--red) 60%)}

/* gallery */
.gallery{top:2367px;left:0;width:1200px;height:687px}
.gallery .center-title{top:70px}
.shot{position:absolute}

/* certificates */
.certs{top:3054px;left:0;width:1200px;height:297px;background:linear-gradient(90deg,var(--red) 0%,#c40c08 50%,var(--red-dark) 100%)}
.certs .center-title{top:50px;color:var(--white);font-family:var(--heading);font-size:32px}
.certs .center-title::after{background:var(--white)}
.badge{position:absolute}

/* contact */
.contact{top:3351px;left:0;width:1200px;height:625px}
.contact .center-title{top:65px}
.field{position:absolute;height:44px;background:var(--field);border:1px solid var(--field-line);border-radius:3px;font-size:11px;color:#9a9a9a;padding:14px 16px}
.contact .btn{position:absolute;left:529px;top:503px;width:142px;height:42px}

/* appointment */
.appt{top:3976px;left:0;width:1200px;height:404px;background:linear-gradient(90deg,var(--red) 0%,#c40c08 50%,var(--red-dark) 100%)}
.appt h2{position:absolute;left:0;width:1200px;top:56px;text-align:center;font-family:var(--heading);font-size:31px;font-weight:400}
.appt .call{position:absolute;left:290px;top:136px;display:flex;gap:14px;align-items:center}
.appt .call small{display:block;font-size:14px;font-weight:500}
.appt .call strong{display:block;font-size:27px;font-weight:500}
.appt .or{position:absolute;left:664px;top:142px;font-size:24px;font-style:italic}
.appt .btn{position:absolute;left:764px;top:144px;width:174px;height:48px}

/* footer */
.footer{top:4200px;left:0;width:1200px;height:484px}
.foot-name{position:absolute;left:150px;top:230px;width:170px;text-align:center;font-family:var(--heading);font-size:22px}
.socials{position:absolute;left:163px;top:343px;display:flex;gap:11px}
.socials i{width:27px;height:27px;background:var(--white);border-radius:3px}
.fcol{position:absolute;top:190px;font-size:11.5px}
.fcol h4{font-size:14px;font-weight:700;margin-bottom:16px}
.fcol li{list-style:none;line-height:24px;color:var(--muted)}
.fcontact{display:flex;gap:10px;margin-bottom:10px}
.fcontact b{display:block;font-size:10px}
.fcontact span{display:block;line-height:17px;color:var(--muted)}
.copyright{position:absolute;left:0;width:1200px;top:436px;text-align:center;font-size:12px;color:var(--muted)}
.to-top{position:absolute;left:1088px;top:387px;width:32px;height:32px;border-radius:50%;background:var(--red);display:flex;align-items:center;justify-content:center}
</style>
</head>
<body>
<div class="page">

  <div class="abs topbar">
    <span style="left:145px">
      <svg width="11" height="11" viewBox="0 0 24 24"><path fill="#fff" d="M6.6 10.8a15.1 15.1 0 0 0 6.6 6.6l2.2-2.2c.3-.3.7-.4 1-.2 1.1.4 2.3.6 3.6.6.6 0 1 .4 1 1V20c0 .6-.4 1-1 1A17 17 0 0 1 3 4c0-.6.4-1 1-1h3.5c.6 0 1 .4 1 1 0 1.3.2 2.5.6 3.6.1.3 0 .7-.2 1z"/></svg>555.289.0147
    </span>
    <span style="left:278px">
      <svg width="12" height="10" viewBox="0 0 24 18"><rect width="24" height="18" rx="2" fill="#fff"/><path d="M2 2l10 8 10-8" stroke="#e3120b" stroke-width="2" fill="none"/></svg>KestrelAutoLLC@mailbox.test
    </span>
    <span style="right:145px">
      <svg width="11" height="11" viewBox="0 0 24 24"><circle cx="12" cy="12" r="10" fill="none" stroke="#fff" stroke-width="3"/><path d="M12 6v6l4 2" stroke="#fff" stroke-width="2.5" fill="none"/></svg>Hours of Operation: M-F 8:30-6pm
    </span>
  </div>

  <nav class="abs nav">
    <a style="left:144px">Home</a>
    <a style="left:202px">About Us</a>
    <a style="left:280px">Vehicles</a>
    <a style="left:353px">Services</a>
    <a style="left:427px">Locations</a>
    <a style="left:705px">Shop Tours</a>
    <a style="left:796px">Blog</a>
    <a style="left:843px">Careers</a>
    <a class="btn">Schedule Service</a>
  </nav>
  <div class="abs logo-plate">
    <svg width="164" height="218" viewBox="0 0 164 218"><polygon points="82,0 164,40 164,170 82,218 0,170 0,40" fill="#0d0d0d" stroke="#3b3b3b" stroke-width="3"/></svg>
    <div class="logo-name">KESTREL</div>
  </div>

  <section class="abs hero">
    <div class="hero-photo" role="img" aria-label="Red Omvar crossover parked on a rocky shore at dusk"></div>
    <h1><span class="red">KESTREL</span><br>AUTOMOTIVE</h1>
    <p>Kestrel Automotive is a locally owned and operated auto repair shop in Fairdale that offers comprehensive car care and services for Navoro &amp; Omvar and all other Asian imports vehicles.</p>
    <a class="btn">SCHEDULE SERVICE
      <svg width="13" height="13" viewBox="0 0 24 24"><circle cx="12" cy="12" r="11" fill="#fff"/><path d="M10 7l5 5-5 5" stroke="#e3120b" stroke-width="3" fill="none"/></svg></a>
    <svg class="abs" style="left:0;top:0" width="1200" height="746" viewBox="0 0 1200 746">
      <path d="M0 572 L600 746 L1200 572 L1200 628 L600 746 L0 628Z" fill="#9d9d9d"/>
      <path d="M0 628 L600 746 L1200 628 L1200 746 L0 746Z" fill="#000"/>
    </svg>
    <div class="dots"><i></i><i></i><i class="on"></i><i></i><i></i></div>
  </section>

  <section class="abs about">
    <div class="abs frame-back"></div>
    <div class="abs photo-a" role="img" aria-label="SUV raised on a lift inside the repair shop"></div>
    <div class="abs photo-b" role="img" aria-label="Technicians working on an engine assembly"></div>
    <h2 class="title">ABOUT <span class="w">US</span><span class="title-rule"></span></h2>
    <div class="copy">
      <p>Led by an NCT master certified technician with 20 years experience working for Navoro &amp; Omvar dealerships, our auto shop is your go to facility for everything from factory auto maintenance, including oil changes, fluid services and tune ups, to complex engine repairs, hybrid diagnostic &amp; repair, brake jobs, etc.</p>
      <p>We have state of the art equipment and tools to ensure that we can properly diagnose and repair your vehicle to get you back on the road quickly. Our work comes with a warranty and is fixed right the first time. We also offer discounts for RideGo &amp; Hoppa rides.</p>
    </div>
    <a class="btn">READ MORE
      <svg width="13" height="13" viewBox="0 0 24 24"><circle cx="12" cy="12" r="11" fill="#fff"/><path d="M10 7l5 5-5 5" stroke="#e3120b" stroke-width="3" fill="none"/></svg></a>
  </section>

  <section class="abs brands">
    <h2 class="title">OUR <span class="w">BRANDS</span><span class="title-rule"></span></h2>
    <p class="lead">Kestrel Automotive specializes in Navoro &amp; Omvar auto repair but also service and repair the following makes</p>
    <div class="brand" style="left:143px;top:217px"><i></i>Hoshiro</div>
    <div class="brand" style="left:298px;top:217px"><i></i>Daeyang</div>
    <div class="brand" style="left:469px;top:217px"><i></i>Arcell</div>
    <div class="brand" style="left:143px;top:299px"><i></i>Kyrro</div>
    <div class="brand" style="left:298px;top:299px"><i></i>Nakamo</div>
    <div class="brand" style="left:469px;top:299px"><i></i>Mizora</div>
    <div class="brand" style="left:143px;top:381px"><i></i>Inveris</div>
    <div class="brand" style="left:298px;top:381px"><i></i>Marendo</div>
    <svg class="abs" style="left:640px;top:33px" width="560" height="457" viewBox="0 0 560 457" role="img" aria-label="White Omvar SUV in the shop bay">
      <defs>
        <linearGradient id="bay" x1="0" y1="0" x2="0" y2="1"><stop offset="0" stop-color="#d8dadc"/><stop offset=".55" stop-color="#b9bcbf"/><stop offset=".75" stop-color="#6f6a62"/><stop offset="1" stop-color="#3a3632"/></linearGradient>
        <radialGradient id="suvbody" cx=".55" cy=".52" r=".45"><stop offset="0" stop-color="#f4f5f6"/><stop offset=".7" stop-color="#dfe1e3" stop-opacity=".8"/><stop offset="1" stop-color="#c0c3c6" stop-opacity="0"/></radialGradient>
      </defs>
      <polygon points="124,0 560,0 560,457 124,457 14,225" fill="#8a8a8a"/>
      <polygon points="132,0 560,0 560,457 132,457 26,225" fill="url(#bay)"/>
      <polygon points="132,0 560,0 560,457 132,457 26,225" fill="url(#suvbody)"/>
    </svg>
  </section>

  <section class="abs services">
    <h2 class="center-title title"><span class="dim">OUR</span> <span class="w">SERVICES</span></h2>
    <svg width="0" height="0" style="position:absolute"><symbol id="star" viewBox="0 0 24 24"><path fill="#fff" d="M12 1l3.2 7 7.6.7-5.8 5 1.8 7.5L12 17.3 5.2 21.2 7 13.7l-5.8-5 7.6-.7z"/></symbol></svg>
    <div class="svc" style="left:145px;top:157px"><svg width="18" height="18"><use href="#star"/></svg>Oil Changes</div>
    <div class="svc" style="left:145px;top:200px"><svg width="18" height="18"><use href="#star"/></svg>Tire Balance &amp; Rotations</div>
    <div class="svc" style="left:145px;top:243px"><svg width="18" height="18"><use href="#star"/></svg>Emission Repair &amp;<br>Catalytic Converters</div>
    <div class="svc" style="left:145px;top:308px"><svg width="18" height="18"><use href="#star"/></svg>Brakes Service &amp; Repair</div>
    <div class="svc" style="left:373px;top:157px"><svg width="18" height="18"><use href="#star"/></svg>Computer Diagnostics</div>
    <div class="svc" style="left:373px;top:200px"><svg width="18" height="18"><use href="#star"/></svg>Pre Purchase Inspections</div>
    <div class="svc" style="left:373px;top:243px"><svg width="18" height="18"><use href="#star"/></svg>Suspension Service &amp;<br>Repair</div>
    <div class="svc" style="left:373px;top:308px"><svg width="18" height="18"><use href="#star"/></svg>Engine Repair</div>
    <div class="svc" style="left:613px;top:157px"><svg width="18" height="18"><use href="#star"/></svg>Electrical Specialists</div>
    <div class="svc" style="left:613px;top:200px"><svg width="18" height="18"><use href="#star"/></svg>Electrical Specialists</div>
    <div class="svc" style="left:613px;top:243px"><svg width="18" height="18"><use href="#star"/></svg>Leveling Kits &amp; Minor<br>Lift Kit installation</div>
    <div class="svc" style="left:613px;top:308px"><svg width="18" height="18"><use href="#star"/></svg>Heating &amp; AC Repair</div>
    <div class="svc" style="left:829px;top:157px"><svg width="18" height="18"><use href="#star"/></svg>Tires</div>
    <div class="svc" style="left:829px;top:200px"><svg width="18" height="18"><use href="#star"/></svg>Insurance Claims</div>
    <div class="svc" style="left:829px;top:243px"><svg width="18" height="18"><use href="#star"/></svg>Exhaust, Muffler Service &amp;<br>Repair</div>
    <div class="svc" style="left:829px;top:308px"><svg width="18" height="18"><use href="#star"/></svg>State Inspection</div>
    <a class="btn">VIEW ALL SERVICES
      <svg width="13" height="13" viewBox="0 0 24 24"><circle cx="12" cy="12" r="11" fill="#fff"/><path d="M10 7l5 5-5 5" stroke="#e3120b" stroke-width="3" fill="none"/></svg></a>
  </section>

  <section class="abs gallery">
    <h2 class="center-title title">OUR <span class="w">GALLERY</span></h2>
    <div class="shot" style="left:144px;top:166px;width:220px;height:436px;background:linear-gradient(90deg,#c9b98f 0%,#e2d6b4 35%,#b8a77c 55%,#2a2a2c 75%,#4b5a72 100%)" role="img" aria-label="Sedan with an open door in the service bay"></div>
    <div class="shot" style="left:376px;top:166px;width:448px;height:212px;background:radial-gradient(ellipse 120px 50px at 320px 30px,#c52a22,transparent 80%),linear-gradient(170deg,#b7bcc2 0%,#6a6e74 40%,#2b2d31 70%,#17181b 100%)" role="img" aria-label="Engine bay opened for repair"></div>
    <div class="shot" style="left:376px;top:390px;width:217px;height:212px;background:radial-gradient(ellipse 80px 60px at 110px 120px,#8a8f96,transparent 80%),linear-gradient(160deg,#2f4d86 0%,#3f4450 45%,#1a1b1e 100%)" role="img" aria-label="Engine parts removed during an overhaul"></div>
    <div class="shot" style="left:605px;top:390px;width:219px;height:212px;background:radial-gradient(ellipse 90px 60px at 120px 140px,#0e0e10,transparent 85%),linear-gradient(90deg,#2f55a8 0 10%,#8f949b 10% 80%,#2f55a8 80% 88%,#6a6e75 88%)" role="img" aria-label="Black SUV on a lift"></div>
    <div class="shot" style="left:836px;top:166px;width:219px;height:436px;background:radial-gradient(ellipse 90px 110px at 110px 200px,#4e5258,transparent 80%),linear-gradient(180deg,#d7dadd 0%,#8c9096 35%,#55585e 65%,#b3170f 82%,#7a6a5a 100%)" role="img" aria-label="Engine block on a red stand"></div>
  </section>

  <section class="abs certs">
    <h2 class="center-title">CERTIFICATE &amp; INSTALLER</h2>
    <div class="badge" style="left:254px;top:168px;width:92px;height:46px;background:#f2f2f2;border-radius:6px"></div>
    <div class="badge" style="left:436px;top:173px;width:128px;height:36px;background:#f2f2f2;border-radius:4px"></div>
    <div class="badge" style="left:648px;top:140px;width:104px;height:104px;background:#f2f2f2;border-radius:50%"></div>
    <div class="badge" style="left:849px;top:143px;width:98px;height:98px;background:#f2f2f2;border-radius:50%"></div>
  </section>

  <section class="abs contact">
    <h2 class="center-title title">CONTACT <span class="w">US</span></h2>
    <div class="field" style="left:144px;top:174px;width:294px">Name</div>
    <div class="field" style="left:453px;top:174px;width:292px">Phone</div>
    <div class="field" style="left:760px;top:174px;width:295px">Email Address</div>
    <div class="field" style="left:144px;top:239px;width:447px">Year</div>
    <div class="field" style="left:607px;top:239px;width:448px">Make</div>
    <div class="field" style="left:144px;top:305px;width:447px">Model</div>
    <div class="field" style="left:607px;top:305px;width:448px">Services
      <svg style="position:absolute;right:18px;top:19px" width="10" height="6" viewBox="0 0 10 6"><path d="M0 0h10L5 6z" fill="#bbb"/></svg></div>
    <div class="field" style="left:144px;top:370px;width:911px;height:85px">Message</div>
    <a class="btn">SUBMIT
      <svg width="13" height="13" viewBox="0 0 24 24"><circle cx="12" cy="12" r="11" fill="#fff"/><path d="M10 7l5 5-5 5" stroke="#e3120b" stroke-width="3" fill="none"/></svg></a>
  </section>

  <section class="abs appt">
    <h2>SCHEDULE AN APPOINTMENT</h2>
    <div class="call">
      <svg width="40" height="40" viewBox="0 0 40 40"><circle cx="20" cy="20" r="19" fill="#fff"/><path transform="translate(9 9) scale(.92)" fill="#e3120b" d="M6.6 10.8a15.1 15.1 0 0 0 6.6 6.6l2.2-2.2c.3-.3.7-.4 1-.2 1.1.4 2.3.6 3.6.6.6 0 1 .4 1 1V20c0 .6-.4 1-1 1A17 17 0 0 1 3 4c0-.6.4-1 1-1h3.5c.6 0 1 .4 1 1 0 1.3.2 2.5.6 3.6.1.3 0 .7-.2 1z"/></svg>
      <div><small>Contact us for a free estimate!</small><strong>Call: 555.013.9110</strong></div>
    </div>
    <svg class="abs" style="left:622px;top:106px" width="116" height="30" viewBox="0 0 116 30"><path d="M2 26 C30 4 80 2 110 12" stroke="#fff" stroke-width="2" fill="none"/><path d="M102 6l9 6-10 4" stroke="#fff" stroke-width="2" fill="none"/></svg>
    <div class="or">or</div>
    <a class="btn">FREE ESTIMATE
      <svg width="13" height="13" viewBox="0 0 24 24"><circle cx="12" cy="12" r="11" fill="#fff"/><path d="M10 7l5 5-5 5" stroke="#e3120b" stroke-width="3" fill="none"/></svg></a>
  </section>

  <footer class="abs footer">
    <svg class="abs" style="left:0;top:0" width="1200" height="484" viewBox="0 0 1200 484">
      <path d="M0 180 L600 30 L1200 180 L1200 200 L600 52 L0 200Z" fill="#8d8d8d"/>
      <path d="M0 200 L600 52 L1200 200 L1200 484 L0 484Z" fill="#141414"/>
    </svg>
    <div class="foot-name">KESTREL</div>
    <div class="socials"><i></i><i></i><i></i><i></i></div>
    <div class="fcol" style="left:445px">
      <h4>Quick Links</h4>
      <ul><li>Home</li><li>About Us</li><li>Services</li><li>Our Projects</li><li>Contact Us</li></ul>
    </div>
    <div class="fcol" style="left:624px">
      <h4>About Company</h4>
      <ul><li>Terms of Use</li><li>Terms &amp; Condition</li><li>Areas We Serve</li><li>Careers</li><li>Sitemap</li></ul>
    </div>
    <div class="fcol" style="left:833px">
      <h4>Contact Us</h4>
      <div class="fcontact"><svg width="10" height="13" viewBox="0 0 20 26"><path fill="#e3120b" d="M10 0a10 10 0 0 1 10 10c0 7-10 16-10 16S0 17 0 10A10 10 0 0 1 10 0zm0 6a4 4 0 1 0 0 8 4 4 0 0 0 0-8z"/></svg><div><b>Location</b><span>412 Harbor Park Circle #5 Fairdale,<br>TX 75000</span></div></div>
      <div class="fcontact"><svg width="11" height="11" viewBox="0 0 24 24"><path fill="#e3120b" d="M6.6 10.8a15.1 15.1 0 0 0 6.6 6.6l2.2-2.2c.3-.3.7-.4 1-.2 1.1.4 2.3.6 3.6.6.6 0 1 .4 1 1V20c0 .6-.4 1-1 1A17 17 0 0 1 3 4c0-.6.4-1 1-1h3.5c.6 0 1 .4 1 1 0 1.3.2 2.5.6 3.6.1.3 0 .7-.2 1z"/></svg><div><b>Phone</b><span>555.013.9110</span></div></div>
      <div class="fcontact"><svg width="12" height="10" viewBox="0 0 24 18"><rect width="24" height="18" rx="2" fill="#e3120b"/><path d="M2 2l10 8 10-8" stroke="#141414" stroke-width="2" fill="none"/></svg><div><b>Email</b><span>KestrelAutoLLC@mailbox.test</span></div></div>
    </div>
    <div class="to-top"><svg width="12" height="8" viewBox="0 0 12 8"><path d="M1 7l5-5 5 5" stroke="#fff" stroke-width="2" fill="none"/></svg></div>
    <div class="copyright">2024 Copyright - Kestrel Automotive LLC &nbsp;| All Rights Reserved</div>
  </footer>

</div>
</body>
</html>
```